Webdesign für industrielle Produktion von Suppen, Saucen, Bouillons und Konzentraten
Zielgruppe
Industrielle Produktion von Suppen, Saucen, Bouillons und Konzentraten
Aufgabenstellung
Aufmachung nicht zu modern, eher klassisch Understatement

```html
<!DOCTYPE html>
<html lang="de">
<head>
<meta charset="utf-8">
<title>Talbrook – Geschäft</title>
<link href="https://fonts.googleapis.com/css2?family=Urbanist:wght@400;500;600;700;800&display=swap" rel="stylesheet">
<style>
:root{
  --red:#d1101a;
  --red-dark:#8e0a10;
  --red-deep:#5e0508;
  --ink:#111;
  --muted:#2a2a2a;
  --line:#d9d9d9;
  --white:#fff;
  --chip:#f0f0f0;
}
*{box-sizing:border-box;margin:0;padding:0}
html,body{width:1200px;height:2366px;overflow:hidden}
body{font-family:"Urbanist",sans-serif;color:var(--ink);background:var(--white);position:relative}

.hero{position:absolute;left:0;top:0;width:1200px;height:412px;
  background:radial-gradient(ellipse at 50% 40%,#e0141e 0%,#b80c14 55%,#8c070d 100%);text-align:center;color:var(--white)}
.nav-ribbon{position:absolute;top:40px;left:86px;width:1028px;height:68px;background:var(--white);display:flex;align-items:center;font-size:14px;font-weight:500}
.ribbon-tail{position:absolute;top:52px;width:40px;height:64px;background:#e6e6e6}
.ribbon-tail.left{left:60px;clip-path:polygon(0 0,100% 0,100% 100%,20% 100%,40% 50%)}
.ribbon-tail.right{right:60px;clip-path:polygon(0 0,100% 0,60% 50%,80% 100%,0 100%)}
.nav-links{display:flex;gap:16px;margin-left:13px}
.nav-links a{color:var(--ink);text-decoration:none}
.nav-links a.active{color:var(--red);font-weight:600}
.brand-tab{position:absolute;left:404px;top:-24px;width:214px;height:116px;border-radius:50%;background:var(--white);display:flex;align-items:center;justify-content:center}
.brand-name{color:var(--red);font-weight:800;font-size:32px;line-height:1}
.nav-contact{position:absolute;left:626px;color:var(--ink)}
.search{position:absolute;left:735px;width:212px;height:34px;border:1.5px solid #777;border-radius:6px;display:flex;align-items:center;padding:0 12px;justify-content:space-between;color:var(--ink)}
.nav-icons{position:absolute;left:966px;display:flex;gap:14px}
.hero .eyebrow{position:absolute;top:166px;width:100%;font-size:18px;font-weight:500}
.hero h1{position:absolute;top:190px;width:100%;font-size:58px;font-weight:800;line-height:80px;letter-spacing:.2px}

.filters{position:absolute;top:493px;left:60px;display:flex;gap:19px}
.filter label{display:block;font-size:18px;font-weight:600;margin-bottom:7px}
.select{width:256px;height:46px;border:2px solid #333;border-radius:4px;display:flex;align-items:center;justify-content:space-between;padding:0 15px;font-size:14px;font-weight:500}

.grid{position:absolute;top:611px;left:60px;display:grid;grid-template-columns:repeat(4,256px);gap:18px;row-gap:18px}
.card{height:375px;border:2px solid #ececec;border-radius:10px;padding:8px;position:relative;box-shadow:0 2px 4px rgba(0,0,0,.06);display:flex;flex-direction:column}
.card.featured{background:linear-gradient(180deg,var(--red) 0%,var(--red-deep) 100%);border-color:var(--red);color:var(--white)}
.product-photo{height:183px;border-radius:6px;background:radial-gradient(ellipse at 50% 55%,#e9c56a 0%,#c33a2a 35%,#efefef 70%)}
.product-photo.gold{background:radial-gradient(ellipse at 50% 55%,#c8a04a 0%,#8a5a20 35%,#efefef 70%)}
.product-photo.blue{background:radial-gradient(ellipse at 50% 55%,#e5d7a0 0%,#2a5aa0 35%,#efefef 70%)}
.product-photo.dark{background:radial-gradient(ellipse at 50% 55%,#c24a2a 0%,#3a3a3a 35%,#efefef 70%)}
.product-photo.cream{background:radial-gradient(ellipse at 50% 55%,#e8dcc0 0%,#b08a4a 35%,#efefef 70%)}
.featured .product-photo{background:radial-gradient(ellipse at 50% 55%,#6ea23a 0%,#2e6b2a 35%,#fff 70%)}
.heart{position:absolute;top:15px;right:15px;width:28px;height:28px;border-radius:50%;background:#111;display:flex;align-items:center;justify-content:center}
.card h3{font-size:19px;font-weight:600;margin-top:13px;line-height:22px}
.card p{font-size:14px;line-height:16.5px;margin-top:2px}
.price{font-size:18px;font-weight:700;margin-top:8px}
.actions{display:flex;justify-content:space-between;align-items:center;margin-top:auto;margin-bottom:2px}
.btn-details{width:161px;height:39px;border:2px solid #111;border-radius:5px;display:flex;align-items:center;justify-content:center;font-size:14px;font-weight:500;background:var(--white);color:var(--ink)}
.featured .btn-details{border-color:var(--white)}
.btn-cart{width:45px;height:36px;border:2px solid #111;border-radius:5px;display:flex;align-items:center;justify-content:center;background:var(--white);margin-right:2px}

.pagination{position:absolute;top:1818px;left:60px;width:1080px;height:46px}
.page-btn{position:absolute;top:5px;height:35px;border:2px solid #999;border-radius:6px;display:flex;align-items:center;gap:8px;padding:0 15px;font-size:14px;font-weight:500}
.pages{position:absolute;left:364px;top:0;display:flex;font-size:16px;font-weight:500}
.pages span{width:47px;height:46px;margin-right:4px;display:flex;align-items:center;justify-content:center;color:#777}
.pages span.current{background:var(--chip);border-radius:6px;color:var(--ink);font-weight:700}

.footer{position:absolute;top:1946px;left:0;width:1200px;height:420px;color:var(--white);
  background:radial-gradient(ellipse at 40% 40%,#c0141a 0%,#8a0a0e 60%,#5c0508 100%)}
.footer-brand{position:absolute;left:60px;top:84px;font-weight:800;font-size:40px;line-height:1;color:var(--white)}
.footer-about{position:absolute;left:60px;top:174px;width:310px;font-size:14px;line-height:16.5px}
.payments{position:absolute;left:60px;top:258px;display:flex;gap:16px}
.payments span{width:37px;height:24px;background:var(--white);border-radius:3px}
.newsletter-title{position:absolute;left:609px;top:80px;font-size:19px;font-weight:500;line-height:22px}
.newsletter{position:absolute;left:819px;top:71px;width:322px;height:42px;background:var(--white);border-radius:4px;display:flex;align-items:center;justify-content:space-between;color:var(--ink);font-size:14px;padding-left:27px;overflow:hidden}
.newsletter b{width:50px;height:42px;background:var(--red);display:flex;align-items:center;justify-content:center}
.col{position:absolute;top:150px;font-size:14px}
.col h4{font-size:19px;font-weight:500;margin-bottom:26px}
.col li{list-style:none;margin-bottom:11px}
.footer-rule{position:absolute;left:60px;top:354px;width:1080px;height:2px;background:rgba(255,255,255,.8)}
.social{position:absolute;left:60px;top:382px;display:flex;gap:9px}
.social span{width:16px;height:16px;border-radius:50%;background:var(--white)}
.copyright{position:absolute;right:60px;top:384px;font-size:11px}
</style>
</head>
<body>

<header class="hero">
  <div class="ribbon-tail left"></div>
  <div class="ribbon-tail right"></div>
  <nav class="nav-ribbon">
    <div class="nav-links">
      <a class="active" href="#">Geschäft</a>
      <a href="#">GV-Produkte</a>
      <a href="#">Catering-Produkte</a>
      <a href="#">Nachricht</a>
    </div>
    <div class="brand-tab"><span class="brand-name">Talbrook</span></div>
    <a class="nav-contact">Kontakt</a>
    <div class="search">Hier Suchen
      <svg width="18" height="18" viewBox="0 0 24 24" fill="none" stroke="#111" stroke-width="2"><circle cx="10" cy="10" r="7"/><path d="M15 15l6 6"/></svg>
    </div>
    <div class="nav-icons">
      <svg width="20" height="20" viewBox="0 0 24 24" fill="none" stroke="#111" stroke-width="2"><circle cx="12" cy="8" r="4"/><path d="M4 21c1-5 15-5 16 0"/></svg>
      <svg width="22" height="20" viewBox="0 0 24 24" fill="none" stroke="#111" stroke-width="2"><path d="M2 3h3l2 12h12l2-9H6"/><circle cx="9" cy="20" r="1.5"/><circle cx="17" cy="20" r="1.5"/></svg>
    </div>
  </nav>
  <div class="eyebrow">Geschäft</div>
  <h1>Ihre Lieblingsfunde, Alles An<br>Einem Ort</h1>
</header>

<section class="filters">
  <div class="filter"><label>Kategorien</label><div class="select">Suppen <svg width="10" height="6" viewBox="0 0 10 6"><path d="M1 1l4 4 4-4" stroke="#333" stroke-width="1.5" fill="none"/></svg></div></div>
  <div class="filter"><label>Preis</label><div class="select">Alle Preise <svg width="10" height="6" viewBox="0 0 10 6"><path d="M1 1l4 4 4-4" stroke="#333" stroke-width="1.5" fill="none"/></svg></div></div>
  <div class="filter"><label>Wählen Sie Ihren Typ Aus</label><div class="select">Nicht-Vegetarisch <svg width="10" height="6" viewBox="0 0 10 6"><path d="M1 1l4 4 4-4" stroke="#333" stroke-width="1.5" fill="none"/></svg></div></div>
</section>

<main class="grid">
  <article class="card featured">
    <div class="product-photo" role="img" aria-label="Produktfoto: Dosen klare Gemüsesuppe"></div>
    <span class="heart"><svg width="14" height="13" viewBox="0 0 24 22" fill="none" stroke="#fff" stroke-width="2.5"><path d="M12 20S2 13 2 7a5 5 0 0 1 10-1 5 5 0 0 1 10 1c0 6-10 13-10 13z"/></svg></span>
    <h3>Clear Vegetable Soup</h3>
    <p>Lorem Ipsum Dolor Sit Amet Consectetur. Sem In Mollis Lacus Semper Amet Duis Egestas.</p>
    <div class="price">8,88 €</div>
    <div class="actions"><span class="btn-details">More Details</span><span class="btn-cart"><svg width="18" height="16" viewBox="0 0 24 22" fill="none" stroke="#111" stroke-width="2"><path d="M1 2h3l2 12h13l2-9H6"/><path d="M11 8v4M15 8v4"/><circle cx="9" cy="19" r="1.5"/><circle cx="17" cy="19" r="1.5"/></svg></span></div>
  </article>
  <article class="card">
    <div class="product-photo gold" role="img" aria-label="Produktfoto: Dosen Rindbouillon"></div>
    <h3>Beef Bouillon – 10 Kg</h3>
    <p>Lorem Ipsum Dolor Sit Amet Consectetur. Sem In Mollis Lacus Semper Amet Duis Egestas.</p>
    <div class="price">123,05 €</div>
    <div class="actions"><span class="btn-details">More Details</span><span class="btn-cart"><svg width="18" height="16" viewBox="0 0 24 22" fill="none" stroke="#111" stroke-width="2"><path d="M1 2h3l2 12h13l2-9H6"/><path d="M11 8v4M15 8v4"/><circle cx="9" cy="19" r="1.5"/><circle cx="17" cy="19" r="1.5"/></svg></span></div>
  </article>
  <article class="card">
    <div class="product-photo" role="img" aria-label="Produktfoto: Dosen Gulaschsuppe"></div>
    <h3>Hungarian Goulash Soup</h3>
    <p>Lorem Ipsum Dolor Sit Amet Consectetur. Sem In Mollis Lacus Semper Amet Duis Egestas.</p>
    <div class="price">26,22 €</div>
    <div class="actions"><span class="btn-details">More Details</span><span class="btn-cart"><svg width="18" height="16" viewBox="0 0 24 22" fill="none" stroke="#111" stroke-width="2"><path d="M1 2h3l2 12h13l2-9H6"/><path d="M11 8v4M15 8v4"/><circle cx="9" cy="19" r="1.5"/><circle cx="17" cy="19" r="1.5"/></svg></span></div>
  </article>
  <article class="card">
    <div class="product-photo" role="img" aria-label="Produktfoto: Dosen Gulaschsuppe Royal"></div>
    <h3>Ung. Gulaschsuppe Royal</h3>
    <p>Lorem Ipsum Dolor Sit Amet Consectetur. Sem In Mollis Lacus Semper Amet Duis Egestas.</p>
    <div class="price">7,60 €</div>
    <div class="actions"><span class="btn-details">More Details</span><span class="btn-cart"><svg width="18" height="16" viewBox="0 0 24 22" fill="none" stroke="#111" stroke-width="2"><path d="M1 2h3l2 12h13l2-9H6"/><path d="M11 8v4M15 8v4"/><circle cx="9" cy="19" r="1.5"/><circle cx="17" cy="19" r="1.5"/></svg></span></div>
  </article>

  <article class="card">
    <div class="product-photo" role="img" aria-label="Produktfoto: Dosen Rinderfond"></div>
    <h3>RindFleischSuppe – 1/1</h3>
    <p>Lorem Ipsum Dolor Sit Amet Consectetur. Sem In Mollis Lacus Semper Amet Duis Egestas.</p>
    <div class="price">8,88 €</div>
    <div class="actions"><span class="btn-details">More Details</span><span class="btn-cart"><svg width="18" height="16" viewBox="0 0 24 22" fill="none" stroke="#111" stroke-width="2"><path d="M1 2h3l2 12h13l2-9H6"/><path d="M11 8v4M15 8v4"/><circle cx="9" cy="19" r="1.5"/><circle cx="17" cy="19" r="1.5"/></svg></span></div>
  </article>
  <article class="card">
    <div class="product-photo blue" role="img" aria-label="Produktfoto: Dosen klare Fischsuppe"></div>
    <h3>Beef Bouillon – 10 Kg</h3>
    <p>Lorem Ipsum Dolor Sit Amet Consectetur. Sem In Mollis Lacus Semper Amet Duis Egestas.</p>
    <div class="price">123,05 €</div>
    <div class="actions"><span class="btn-details">More Details</span><span class="btn-cart"><svg width="18" height="16" viewBox="0 0 24 22" fill="none" stroke="#111" stroke-width="2"><path d="M1 2h3l2 12h13l2-9H6"/><path d="M11 8v4M15 8v4"/><circle cx="9" cy="19" r="1.5"/><circle cx="17" cy="19" r="1.5"/></svg></span></div>
  </article>
  <article class="card">
    <div class="product-photo" role="img" aria-label="Produktfoto: Dosen Linsensuppe"></div>
    <h3>Linsen-Suppe</h3>
    <p>Lorem Ipsum Dolor Sit Amet Consectetur. Sem In Mollis Lacus Semper Amet Duis Egestas.</p>
    <div class="price">26,22 €</div>
    <div class="actions"><span class="btn-details">More Details</span><span class="btn-cart"><svg width="18" height="16" viewBox="0 0 24 22" fill="none" stroke="#111" stroke-width="2"><path d="M1 2h3l2 12h13l2-9H6"/><path d="M11 8v4M15 8v4"/><circle cx="9" cy="19" r="1.5"/><circle cx="17" cy="19" r="1.5"/></svg></span></div>
  </article>
  <article class="card">
    <div class="product-photo gold" role="img" aria-label="Produktfoto: Dosen Ochsenschwanzsuppe"></div>
    <h3>Geb. Ochsenschwanz</h3>
    <p>Lorem Ipsum Dolor Sit Amet Consectetur. Sem In Mollis Lacus Semper Amet Duis Egestas.</p>
    <div class="price">22,90 €</div>
    <div class="actions"><span class="btn-details">More Details</span><span class="btn-cart"><svg width="18" height="16" viewBox="0 0 24 22" fill="none" stroke="#111" stroke-width="2"><path d="M1 2h3l2 12h13l2-9H6"/><path d="M11 8v4M15 8v4"/><circle cx="9" cy="19" r="1.5"/><circle cx="17" cy="19" r="1.5"/></svg></span></div>
  </article>

  <article class="card">
    <div class="product-photo cream" role="img" aria-label="Produktfoto: Dosen Kartoffelsuppe"></div>
    <h3>Kessel-Gulasch-Suppe</h3>
    <p>Lorem Ipsum Dolor Sit Amet Consectetur. Sem In Mollis Lacus Semper Amet Duis Egestas.</p>
    <div class="price">4,82 €</div>
    <div class="actions"><span class="btn-details">More Details</span><span class="btn-cart"><svg width="18" height="16" viewBox="0 0 24 22" fill="none" stroke="#111" stroke-width="2"><path d="M1 2h3l2 12h13l2-9H6"/><path d="M11 8v4M15 8v4"/><circle cx="9" cy="19" r="1.5"/><circle cx="17" cy="19" r="1.5"/></svg></span></div>
  </article>
  <article class="card">
    <div class="product-photo dark" role="img" aria-label="Produktfoto: Dosen Kesselgulaschsuppe"></div>
    <h3>Kartoffelsuppen-Terrine</h3>
    <p>Lorem Ipsum Dolor Sit Amet Consectetur. Sem In Mollis Lacus Semper Amet Duis Egestas.</p>
    <div class="price">1,82 €</div>
    <div class="actions"><span class="btn-details">More Details</span><span class="btn-cart"><svg width="18" height="16" viewBox="0 0 24 22" fill="none" stroke="#111" stroke-width="2"><path d="M1 2h3l2 12h13l2-9H6"/><path d="M11 8v4M15 8v4"/><circle cx="9" cy="19" r="1.5"/><circle cx="17" cy="19" r="1.5"/></svg></span></div>
  </article>
  <article class="card">
    <div class="product-photo cream" role="img" aria-label="Produktfoto: Dosen Rindfleischsuppe mit Einlage"></div>
    <h3>Hühnersuppe – First Class</h3>
    <p>Lorem Ipsum Dolor Sit Amet Consectetur. Sem In Mollis Lacus Semper Amet Duis Egestas.</p>
    <div class="price">1,82 €</div>
    <div class="actions"><span class="btn-details">More Details</span><span class="btn-cart"><svg width="18" height="16" viewBox="0 0 24 22" fill="none" stroke="#111" stroke-width="2"><path d="M1 2h3l2 12h13l2-9H6"/><path d="M11 8v4M15 8v4"/><circle cx="9" cy="19" r="1.5"/><circle cx="17" cy="19" r="1.5"/></svg></span></div>
  </article>
  <article class="card">
    <div class="product-photo" role="img" aria-label="Produktfoto: Dosen Hühnersuppe Konzentrat"></div>
    <h3>1/1 Hühnersuppe 1:10 Konz.</h3>
    <p>Lorem Ipsum Dolor Sit Amet Consectetur. Sem In Mollis Lacus Semper Amet Duis Egestas.</p>
    <div class="price">8,88 €</div>
    <div class="actions"><span class="btn-details">More Details</span><span class="btn-cart"><svg width="18" height="16" viewBox="0 0 24 22" fill="none" stroke="#111" stroke-width="2"><path d="M1 2h3l2 12h13l2-9H6"/><path d="M11 8v4M15 8v4"/><circle cx="9" cy="19" r="1.5"/><circle cx="17" cy="19" r="1.5"/></svg></span></div>
  </article>
</main>

<nav class="pagination">
  <span class="page-btn" style="left:0"><svg width="14" height="12" viewBox="0 0 14 12" fill="none" stroke="#111" stroke-width="1.6"><path d="M13 6H1M6 1L1 6l5 5"/></svg>Vorherige</span>
  <div class="pages"><span class="current">1</span><span>2</span><span>3</span><span>...</span><span>8</span><span>9</span><span>10</span></div>
  <span class="page-btn" style="right:0">Nächste<svg width="14" height="12" viewBox="0 0 14 12" fill="none" stroke="#111" stroke-width="1.6"><path d="M1 6h12M8 1l5 5-5 5"/></svg></span>
</nav>

<footer class="footer">
  <div class="footer-brand">Talbrook</div>
  <p class="footer-about">Lorem Ipsum Dolor Sit Amet Consectetur. Ut Nulla Pellentesque Turpis Viverra Id Amet Bibendum.</p>
  <div class="payments" aria-label="Zahlungsarten"><span></span><span></span><span></span><span></span><span></span></div>
  <div class="newsletter-title">Abonnieren Sie<br>Unseren Neuen Brief</div>
  <div class="newsletter">Enter Your Email<b><svg width="10" height="16" viewBox="0 0 10 16" fill="none" stroke="#fff" stroke-width="2"><path d="M2 2l6 6-6 6"/></svg></b></div>
  <div class="col" style="left:609px"><h4>Company</h4><ul><li>About Us</li><li>Work With Us</li><li>Blog &amp; News</li></ul></div>
  <div class="col" style="left:842px"><h4>Shop</h4><ul><li>Collections</li><li>Blog Post</li><li>Wishlist</li></ul></div>
  <div class="col" style="left:1056px"><h4>Quick Link</h4><ul><li>Shop</li><li>Products</li><li>Contact</li></ul></div>
  <div class="footer-rule"></div>
  <div class="social" aria-label="Soziale Netzwerke"><span></span><span></span><span></span><span></span></div>
  <div class="copyright">Copyright © 2024 <b>Studio Nordlicht</b>. All Rights Reserved.</div>
</footer>

</body>
</html>
```